BRTL web site redesign

Coastal Linkage Engineering service (BRTL) is a diverse technology company specialising in design and installation of fibre optics, network convergence and building services, for commercial clients in Australia, we required a new design of our website to attract new clients, generate sales leads, and provide information about our services to the market. The site and should have a new technology look and feel and be designed in word press. our branding colour is blue.

Target Market(s)

New developments, Construction organisations, Commercial end users, IT managers, Consultants.

Industry/Entity Type

It Company

Number of Pages Required

5+ page

Font styles to use
Sans Serif

Colors
0292cd
3176b5

Requirements
Must have
• key pages.
• Home page with some sizzle, automated pictures running through, I like the look of this competitor website http://www.gleamwirex.com.au/ good clean menus and easy to navigate.
• Services page our key services are Fibre optics, Security, Building services,Electrical. I would like the same page layout (Design) for all our services, with a find out more link on each page, manly picture driven with text around our key messaging.
• About us page with space for company profile and directors pictures, bio and contact information.
• Certifications / Accreditations page with have over 20 certifications on different products from suppliers, and a number of licences from governing bodies.
• Current and past projects page with case studies and customer outcomes
• Contact us page with options around what services they require more information on, please keep in mind the site is around generating sales Leeds and being seen as an industry expert.
Nice to have
• RSS feeds, Linked in link, to be placed within the design, Consistent BRTL branding,Same colour blue as our logo Document library for education information, white papers, presentations etc,
• a new technology look and feel, mobile friendly.
Should not have
• boring layout, move away from our cuurent website http://www.brtlgroup.com.au/
• no e eCommerce store required.

```html
<!DOCTYPE html>
<html lang="en">
<head>
<meta charset="utf-8">
<title>BRTL Group – Coastal Linkage Engineering service</title>
<link href="https://fonts.googleapis.com/css2?family=Open+Sans:wght@400;600;700&display=swap" rel="stylesheet">
<style>
:root{
  --brand:#0292cd;
  --brand-dark:#3176b5;
  --ink:#222;
  --body:#444;
  --muted:#777;
  --white:#fff;
  --black:#000;
  --footer-text:#8a8a8a;
  --footer-date:#5e5e5e;
}
*{margin:0;padding:0;box-sizing:border-box}
html,body{width:1200px;height:2179px;overflow:hidden}
body{font-family:"Open Sans",Arial,sans-serif;color:var(--body);background:var(--white);position:relative}
.abs{position:absolute}

/* header */
.site-header{position:absolute;left:0;top:0;width:1200px;height:83px;background:var(--white)}
.brand{position:absolute;left:51px;top:18px;display:flex;align-items:center;gap:10px}
.brand-mark{width:38px;height:38px;background:var(--brand)}
.brand-name{font-size:34px;font-weight:700;color:var(--brand);letter-spacing:1px;line-height:1}
.main-nav a{position:absolute;top:30px;font-size:14.5px;color:#666;text-decoration:none}
.main-nav a.active{color:var(--brand-dark)}
.nav-caret{position:absolute;left:807px;top:55px}
.dropdown{position:absolute;left:771px;top:70px;width:106px;height:112px;background:rgba(255,255,255,.9);padding:0 10px;z-index:3}
.dropdown a{display:block;font-size:14px;color:#777;text-decoration:none;line-height:20.5px}
.dropdown a:first-child{margin-top:1px}

/* hero */
.hero{position:absolute;left:0;top:83px;width:1200px;height:562px;
  background:linear-gradient(90deg,#b9bec3 0%,#d9dcdf 25%,#6f7479 45%,#e9ebec 58%,#f4f4f4 70%,#2c2d30 80%,#f2f2f2 100%)}
.hero-arrow{position:absolute;top:252px}

/* about */
.section-title{position:absolute;font-size:23px;font-weight:400;color:var(--ink);text-shadow:0 1px 2px rgba(0,0,0,.25)}
.about-text{position:absolute;left:51px;top:744px;width:1120px;font-size:11.6px;line-height:22px;color:var(--body)}

.service{position:absolute;top:843px;width:245px}
.service-image{width:245px;height:157px;border:2px solid #111;box-shadow:0 3px 4px rgba(0,0,0,.35)}
.service-title{margin-top:22px;font-size:19px;font-weight:600;color:var(--brand);line-height:24px}
.service-text{margin-top:6px;font-size:12.3px;line-height:22px;color:var(--body)}
.btn{display:inline-block;margin-top:14px;width:89px;height:34px;line-height:34px;text-align:center;
  background:linear-gradient(var(--brand),#017fb4);color:var(--white);font-size:11.5px;font-weight:600;
  text-decoration:none;box-shadow:0 3px 3px rgba(0,0,0,.35)}

/* promo */
.promo{position:absolute;left:0;top:1230px;width:1200px;height:323px;
  background:radial-gradient(ellipse at 18% 20%,#1e5a66 0%,#0c2a33 30%,#020608 60%,#000 100%)}
.promo-title{position:absolute;left:0;width:1200px;top:72px;text-align:center;font-size:30px;font-weight:400;color:var(--white)}
.promo-rule{position:absolute;left:238px;top:128px;width:725px;height:1px;background:#5a5a5a}
.promo-text{position:absolute;left:300px;width:600px;top:145px;text-align:center;font-size:13px;line-height:22px;color:var(--white)}
.btn-outline{position:absolute;left:532px;top:210px;width:138px;height:36px;border:2px solid var(--white);
  color:var(--white);font-size:17px;line-height:32px;text-align:center;text-decoration:none;letter-spacing:.5px}

/* projects */
.project{position:absolute;top:1665px;width:290px}
.project-title{font-size:13.8px;color:var(--brand);line-height:20px;font-weight:400}
.project-date{font-size:12px;font-weight:600;color:var(--ink);margin-top:3px}
.project-text{margin-top:8px;font-size:12.2px;line-height:22.5px;color:var(--body)}

/* footer */
.site-footer{position:absolute;left:0;top:1849px;width:1200px;height:330px;background:var(--black)}
.footer-heading{position:absolute;top:17px;font-size:23px;color:var(--white);font-weight:400}
.rss-icon{position:absolute;left:89px;top:26px}
.feed-item{position:absolute;width:280px}
.feed-title{font-size:13px;color:var(--white);line-height:20px}
.feed-date{font-size:11.5px;color:var(--footer-date);line-height:22px}
.feed-text{font-size:11.5px;color:var(--footer-date);line-height:21.5px}
.contact-line{position:absolute;left:917px;font-size:12px;color:var(--footer-text)}
.footer-bar{position:absolute;left:0;top:276px;width:1200px;height:54px;border-top:1px solid #222;
  text-align:center;line-height:52px;font-size:11.5px;color:#b5b5b5}
.footer-bar span{margin:0 9px}
</style>
</head>
<body>

<header class="site-header">
  <div class="brand"><span class="brand-mark"></span><span class="brand-name">BRTL</span></div>
  <nav class="main-nav">
    <a class="active" style="left:619px" href="#">Home</a>
    <a style="left:692px" href="#">About us</a>
    <a style="left:786px" href="#">Services</a>
    <a style="left:876px" href="#">certifications</a>
    <a style="left:991px" href="#">Projects</a>
    <a style="left:1078px" href="#">Contact us</a>
  </nav>
  <svg class="nav-caret" width="9" height="6" viewBox="0 0 9 6"><path d="M0 0h9L4.5 6z" fill="#333"/></svg>
</header>

<div class="dropdown">
  <a href="#">Fibre optics</a>
  <a href="#">Security</a>
  <a href="#">Building<br>services</a>
  <a href="#">Electrical</a>
</div>

<section class="hero" role="img" aria-label="Photo of a man in a suit working on a laptop beside a data centre server rack with yellow and blue cables">
  <svg class="hero-arrow" style="left:6px" width="28" height="28" viewBox="0 0 28 28"><circle cx="14" cy="14" r="12" fill="none" stroke="#ccc" stroke-width="3"/><path d="M17 8l-7 6 7 6" fill="none" stroke="#ccc" stroke-width="3"/></svg>
  <svg class="hero-arrow" style="left:1163px" width="28" height="28" viewBox="0 0 28 28"><circle cx="14" cy="14" r="12" fill="none" stroke="#ccc" stroke-width="3"/><path d="M11 8l7 6-7 6" fill="none" stroke="#ccc" stroke-width="3"/></svg>
</section>

<h2 class="section-title" style="left:54px;top:683px">About BRTL Group</h2>
<p class="about-text">BRTL is diversified technology company 100% Australian owned and operated, we provide Communication, Electrical, Security &amp; ICT services for residential and commercial customers. With over 100 years of combined industry knowledge we pride ourselves on innovated solutions that utilises technology advancements which delivers on our customer’s expectations.</p>

<article class="service" style="left:52px">
  <div class="service-image" role="img" aria-label="Photo of a fibre optic splicing machine with coloured fibres" style="background:linear-gradient(135deg,#3a3d3f,#6a6f73 40%,#c26a2d 60%,#2f3234)"></div>
  <h3 class="service-title">Fibre Optics</h3>
  <p class="service-text">Proin gravida nibh vel velit auctored aliquetenean sollicitudin lorem quis bibendum auctornisi elit.</p>
  <a class="btn" href="#">READ MORE</a>
</article>
<article class="service" style="left:338px">
  <div class="service-image" role="img" aria-label="Photo of white security cameras mounted on a pole" style="background:linear-gradient(135deg,#2a2630,#7c7884 45%,#e4e4e8 60%,#3a3640)"></div>
  <h3 class="service-title">Security</h3>
  <p class="service-text">Proin gravida nibh vel velit auctored aliquetenean sollicitudin lorem quis bibendum auctornisi elit.</p>
  <a class="btn" href="#">READ MORE</a>
</article>
<article class="service" style="left:623px">
  <div class="service-image" role="img" aria-label="Photo of a person touching a glowing blue building control interface" style="background:linear-gradient(135deg,#0a5d9c,#1d8fd4 50%,#5cc2ef 75%,#0b4e88)"></div>
  <h3 class="service-title">Building Services</h3>
  <p class="service-text">Proin gravida nibh vel velit auctored aliquetenean sollicitudin lorem quis bibendum auctornisi elit.</p>
  <a class="btn" href="#">READ MORE</a>
</article>
<article class="service" style="left:905px">
  <div class="service-image" role="img" aria-label="Photo of electrical conduits and wiring in a switchboard" style="background:linear-gradient(135deg,#8c8a86,#d8d6d2 45%,#a9a39b 65%,#5f5c58)"></div>
  <h3 class="service-title">Electrical</h3>
  <p class="service-text">Proin gravida nibh vel velit auctored aliquetenean sollicitudin lorem quis bibendum auctornisi elit.</p>
  <a class="btn" href="#">READ MORE</a>
</article>

<section class="promo" role="img" aria-label="Background photo of glowing blue fibre optic strands on black">
  <h2 class="promo-title">BRTL offers a wide range of IP commercial security solutions</h2>
  <div class="promo-rule"></div>
  <p class="promo-text">Proin gravida nibh vel velit auctor aliquet. Aenean sollicitudin, lorem quis bibendum auctor, nisi elit consequat ipsum, nec sagittis sem nibh id elit.</p>
  <a class="btn-outline" href="#">READ MORE</a>
</section>

<h2 class="section-title" style="left:53px;top:1590px">Current / Past Projects</h2>
<article class="project" style="left:89px">
  <h3 class="project-title">Proin gravida nibh vel velit auctor aliquet</h3>
  <p class="project-date">12 Jan 2015</p>
  <p class="project-text">Lorem Ipsum. Proin gravida nibh vel velit ws uctor aliquet lorem quis bibendum auctor nisi elit consequat ipsum nec sagitti,</p>
</article>
<article class="project" style="left:455px">
  <h3 class="project-title">Gravida nibh vel velit auctor aliquet vild</h3>
  <p class="project-date">12 Jan 2015</p>
  <p class="project-text">Lorem Ipsum. Proin gravida nibh vel velit ws uctor aliquet lorem quis bibendum auctor nisi elit consequat ipsum nec sagitti,</p>
</article>
<article class="project" style="left:835px">
  <h3 class="project-title">Hroin gravida nibh vel velit auctor aliquet</h3>
  <p class="project-date">12 Jan 2015</p>
  <p class="project-text">Lorem Ipsum. Proin gravida nibh vel velit ws uctor aliquet lorem quis bibendum auctor nisi elit consequat ipsum nec sagitti,</p>
</article>

<footer class="site-footer">
  <svg class="rss-icon" width="13" height="13" viewBox="0 0 13 13"><rect width="13" height="13" rx="2" fill="#f08a24"/><circle cx="3.5" cy="9.5" r="1.4" fill="#fff"/><path d="M2.5 6a4.5 4.5 0 0 1 4.5 4.5M2.5 3a7.5 7.5 0 0 1 7.5 7.5" fill="none" stroke="#fff" stroke-width="1.5"/></svg>
  <h2 class="footer-heading" style="left:109px">Rss feed</h2>

  <div class="feed-item" style="left:89px;top:56px">
    <h3 class="feed-title">Aroin gravida nibh vel velit auctor aliquet</h3>
    <p class="feed-date">10 Jan 2015</p>
    <p class="feed-text">Lorem Ipsum. Proin gravida nibh vel velit ws uctor aliquet lorem quis bibendum.</p>
  </div>
  <div class="feed-item" style="left:485px;top:56px">
    <h3 class="feed-title">Aroin gravida nibh vel velit auctor aliquet</h3>
    <p class="feed-date">10 Jan 2015</p>
    <p class="feed-text">Lorem Ipsum. Proin gravida nibh vel velit ws uctor aliquet lorem quis bibendum.</p>
  </div>
  <div class="feed-item" style="left:89px;top:166px">
    <h3 class="feed-title">Aroin gravida nibh vel velit auctor aliquet</h3>
    <p class="feed-date">10 Jan 2015</p>
    <p class="feed-text">Lorem Ipsum. Proin gravida nibh vel velit ws uctor aliquet lorem quis bibendum.</p>
  </div>
  <div class="feed-item" style="left:485px;top:166px">
    <h3 class="feed-title">Aroin gravida nibh vel velit auctor aliquet</h3>
    <p class="feed-date">10 Jan 2015</p>
    <p class="feed-text">Lorem Ipsum. Proin gravida nibh vel velit ws uctor aliquet lorem quis bibendum.</p>
  </div>

  <h2 class="footer-heading" style="left:917px">Contact Details</h2>
  <p class="contact-line" style="top:58px">Suite 4B, 12-14 Harbour Crest Road</p>
  <p class="contact-line" style="top:92px">Westmere NSW 2159</p>
  <p class="contact-line" style="top:125px">PO Box 2284 NSW 1790</p>
  <p class="contact-line" style="top:160px">Telephone 1300 555 019</p>

  <div class="footer-bar">©Copyright 2014 &nbsp;brtlgroup<span>|</span>All rights reserved<span>|</span>Privacy policy<span>|</span>Terms &amp; Conditions</div>
</footer>

</body>
</html>
```